Allied Health team of Physiotherapists & Occupational Therapists seek a business card design

We have our new logo, we now need our new business cards and stationary. Tidewell: Oedema & Family Clinic is seeking a generic card design to represent our whole team and individual cards for each therapist that incorporates our new logo to communicate our holistic approach that is calming, nuturing, supportive and welcoming.
Our Physiotherapists and Occupational Therapists assess, treat and provide education for people who are at risk of or who have lymphoedema. This is often as a result of treatment for cancer. We provide pre-operative and post-operative management and cancer rehabilitation in our Pilates studio. Our team also consists of Physiotherapists who have a strong interest in pelvic floor and continence management for both men and women.

Target Market(s)

Mainly women health conscious

Industry/Entity Type

Allied Health: Physiotherapy / Occupational Therapy

Contact Information for Business Card

Address: 14 Gallivant Ave Seabrook 3377 Phone: 84316570 fax: 8431 6578 Email: info@tidewellcareservices.com.au Website: tidewellcareservices.com.au Facebook address: facebook.com/TidewellOedemaAndFamilyCareClinic. Room to write appointments. Individual cards need to have name, office email and individual email and professional details

Requirements
Must have
• Logo as per uploaded documents

```html
<!DOCTYPE html>
<html lang="en">
<head>
<meta charset="utf-8">
<title>Tidewell Business Card</title>
<link rel="stylesheet" href="https://fonts.googleapis.com/css2?family=Fira+Sans:wght@500&family=Roboto:ital,wght@0,400;0,500;1,400&display=swap">
<style>
  :root {
    --backdrop: #2e2e2e;
    --coral: #df9672;
    --coral-deep: #d88c66;
    --peach: #eeb08c;
    --cream: #f2e9bd;
    --paper: #f3f2f0;
    --sage: #9bb0a2;
    --ink: #2f2f2f;
  }
  * { margin: 0; padding: 0; box-sizing: border-box; }
  html, body { width: 1200px; height: 1138px; overflow: hidden; }
  body { background: var(--backdrop); font-family: "Roboto", sans-serif; position: relative; }

  .card {
    position: absolute;
    border-radius: 14px;
    overflow: hidden;
    box-shadow: 0 4px 12px rgba(0,0,0,0.35);
  }
  .card-front {
    left: 274px; top: 186px; width: 622px; height: 376px;
    background: linear-gradient(135deg, var(--peach) 0%, var(--coral) 45%, var(--coral-deep) 100%);
    display: flex; align-items: center; justify-content: center;
  }
  .card-back {
    left: 276px; top: 608px; width: 618px; height: 374px;
    background: var(--paper);
  }

  .brand {
    text-align: center;
    font-family: "Roboto", sans-serif;
    font-weight: 400;
    line-height: 1.15;
  }
  .card-front .brand { color: var(--cream); }
  .brand .brand-main { display: block; font-size: 44px; }
  .brand .brand-sub { display: block; font-size: 15px; letter-spacing: 2px; text-transform: uppercase; margin-top: 8px; }

  .card-back .brand {
    position: absolute; left: 24px; top: 100px; width: 240px;
    color: var(--coral);
  }
  .card-back .brand .brand-main { font-size: 40px; }
  .card-back .brand .brand-sub { font-size: 13px; }

  .wave { position: absolute; left: 0; top: 0; width: 618px; height: 374px; }

  .person {
    position: absolute; right: 24px; top: 40px;
    text-align: right; color: var(--ink);
  }
  .person-name {
    font-family: "Fira Sans", sans-serif; font-weight: 500;
    font-size: 20px; color: var(--coral); margin-bottom: 6px;
  }
  .person-role { font-size: 14px; font-style: italic; line-height: 21px; }
  .person-focus { font-size: 14px; line-height: 21px; }

  .contact {
    position: absolute; right: 24px; top: 232px;
    list-style: none; text-align: right;
  }
  .contact li {
    font-size: 15px; line-height: 25.5px; color: var(--ink);
    display: flex; justify-content: flex-end; align-items: center; gap: 5px;
  }
  .contact svg { width: 13px; height: 13px; fill: var(--paper); flex: none; }
</style>
</head>
<body>

  <section class="card card-front">
    <div class="brand">
      <span class="brand-main">Tidewell</span>
      <span class="brand-sub">Oedema &amp; Family Clinic</span>
    </div>
  </section>

  <section class="card card-back">
    <svg class="wave" viewBox="0 0 618 374" aria-hidden="true">
      <path d="M0,262 C120,290 250,300 360,250 C450,210 540,185 618,190 L618,374 L0,374 Z" fill="#eeb08c"/>
      <path d="M0,285 C130,320 260,322 370,270 C460,228 545,200 618,198 L618,374 L0,374 Z" fill="#f3f2f0"/>
      <path d="M0,300 C140,334 280,330 380,280 C470,236 550,206 618,204 L618,374 L0,374 Z" fill="#df9672"/>
      <path d="M50,278 C200,300 300,270 390,230 C470,195 550,172 618,172" fill="none" stroke="#9bb0a2" stroke-width="7" stroke-linecap="round"/>
    </svg>

    <div class="brand">
      <span class="brand-main">Tidewell</span>
      <span class="brand-sub">Oedema &amp; Family Clinic</span>
    </div>

    <div class="person">
      <p class="person-name">Maren Ashby</p>
      <p class="person-role">Physiotherapist</p>
      <p class="person-focus">Lymphoedema &amp; Oncology Rehabilitation</p>
      <p class="person-focus">Continence &amp; Pelvic Floor</p>
    </div>

    <ul class="contact">
      <li>8431 6570
        <svg viewBox="0 0 16 16"><path d="M2 6c0-2 3-3 6-3s6 1 6 3v1h-3V6H5v1H2z M4 8h8l1 5H3z"/></svg>
      </li>
      <li>8431 6578
        <svg viewBox="0 0 16 16"><path d="M2 6c0-2 3-3 6-3s6 1 6 3v1h-3V6H5v1H2z M4 8h8l1 5H3z"/></svg>
      </li>
      <li>tidewellcareservices.com.au
        <svg viewBox="0 0 16 16"><path d="M8 1a7 7 0 1 0 0 14A7 7 0 0 0 8 1zm0 1.5c.8 0 1.7 1.6 2 4H6c.3-2.4 1.2-4 2-4zM6 8.5h4c-.2 2.6-1.2 5-2 5s-1.8-2.4-2-5zM2.6 7.5a5.5 5.5 0 0 1 2.4-4 10 10 0 0 0-.8 4zm0 1h1.6a10 10 0 0 0 .8 4 5.5 5.5 0 0 1-2.4-4zm10.8-1h-1.6a10 10 0 0 0-.8-4 5.5 5.5 0 0 1 2.4 4zm0 1a5.5 5.5 0 0 1-2.4 4 10 10 0 0 0 .8-4z"/></svg>
      </li>
      <li>info@tidewellcareservices.com.au
        <svg viewBox="0 0 16 16"><path d="M1 4h14v9H1zm1.5 1.2V12h11V5.2L8 9.2z M2.8 5L8 8.2 13.2 5z"/></svg>
      </li>
      <li>14 Gallivant Ave, Seabrook 3377
        <svg viewBox="0 0 16 16"><path d="M8 1a5 5 0 0 0-5 5c0 3.5 5 9 5 9s5-5.5 5-9a5 5 0 0 0-5-5zm0 7a2 2 0 1 1 0-4 2 2 0 0 1 0 4z"/></svg>
      </li>
    </ul>
  </section>

</body>
</html>
```